Progressive European Honey Business needs minimalistic packaging design

Hello - thank you for your interest in our brief. We are Honey Plinks, a London based Honey business, importing only the best honey Europe has to offer. Our values are deeply rooted with in progressive liberal values and we are looking for minimalist packaging, which reflects that.

We are looking for a design, which dimensions fit with our packaging option (Vessio Glass Jar | HEIGHT 90mm | DIAMETER 63mm). We will require a various output files (High Resolution JPEG (CMYK Colors 300 dpi) Source File Ai, PSD, PDF, Printing files (die cut, die folding) and a 3D Mockup of the packaging for use within digital commerce platforms.

We must be able to adjust the free text on the label front and it should include the following:
Brand Name
Honey type
Limited edition No. X / 100 ( X being the number of purchase i.e. 25 / 100)
EU Honey, Single Orgin (Germany)
(c) The net weight (250g)

The back must include room for additional information (again adjustable by us) and the following:
“Unsuitable for children under 12 months”
(b) The appropriate durability declaration

In total, we are looking for
a) A front label
b) A back label
c) A seal (round) including the attached bee and logo included in the Zip file.
Do note that a) & b) can also be combined into one design as long as the symmetry on the jar stays intact.

The final design should communicate modern aesthetics, high quality, that are slightly provocative and pop off the shelves.

Hi folks, sorry for the delay in completing this project, but my business partner had a leak in his house. We planned to finalise our review today, but this will have to wait until it's no longer raining in his livingroom. Our sincere apologies!

• See branding guidelines

• Must follow the branding guideline and fonts provided as attachment

```html
<!DOCTYPE html>
<html lang="en">
<head>
<meta charset="utf-8">
<title>Honey Plinks – Round Seal</title>
<link rel="stylesheet" href="https://fonts.googleapis.com/css2?family=Montserrat:wght@500&display=swap">
<style>
  :root {
    --bg: #f2f2f2;
    --seal-white: #ffffff;
    --seal-black: #1d1d1b;
    --rim: #222222;
    --brand-orange: #e85e26;
    --bee-yellow: #f6cf3f;
    --bee-dark: #2a2a2a;
  }
  html, body {
    margin: 0;
    width: 1200px;
    height: 750px;
    overflow: hidden;
    background: var(--bg);
  }
  .canvas {
    position: relative;
    width: 1200px;
    height: 750px;
  }
  .seal {
    position: absolute;
    inset: 0;
  }
  .seal__name {
    font-family: "Montserrat", Arial, sans-serif;
    font-weight: 500;
    font-size: 38px;
    fill: var(--brand-orange);
    letter-spacing: 1px;
  }
</style>
</head>
<body>
<main class="canvas">
  <svg class="seal" width="1200" height="750" viewBox="0 0 1200 750" aria-label="Honey Plinks round seal">
    <defs>
      <clipPath id="seal-face">
        <circle cx="600" cy="375" r="330"/>
      </clipPath>
      <linearGradient id="split-shade" x1="0" y1="0" x2="0" y2="1">
        <stop offset="0" stop-color="#ffffff" stop-opacity="0"/>
        <stop offset="1" stop-color="#cfcfcf" stop-opacity="0.8"/>
      </linearGradient>
      <linearGradient id="bee-tone" x1="0" y1="0" x2="1" y2="1">
        <stop offset="0" stop-color="var(--bee-dark)"/>
        <stop offset="0.55" stop-color="var(--bee-yellow)"/>
        <stop offset="1" stop-color="#a9d3ea"/>
      </linearGradient>
    </defs>

    <circle class="seal__rim" cx="600" cy="375" r="352" fill="var(--rim)"/>
    <circle class="seal__rim-inner" cx="600" cy="375" r="338" fill="none" stroke="#3a3a3a" stroke-width="4"/>

    <g clip-path="url(#seal-face)">
      <rect class="seal__field" x="240" y="20" width="720" height="720" fill="var(--seal-white)"/>
      <g transform="translate(600 375) rotate(34)">
        <rect class="seal__shade" x="-500" y="112" width="1000" height="20" fill="url(#split-shade)"/>
        <polygon class="seal__accent-band" points="-500,132 -500,92 -60,132" fill="var(--brand-orange)"/>
        <rect class="seal__black-field" x="-500" y="132" width="1000" height="500" fill="var(--seal-black)"/>
      </g>
      <rect class="seal__mascot" role="img" aria-label="Crowned queen bee mascot illustration"
            x="590" y="160" width="290" height="225" rx="110" fill="url(#bee-tone)" opacity="0.9"/>
      <text class="seal__name" x="575" y="470">Honey Plinks</text>
    </g>
  </svg>
</main>
</body>
</html>
```